Honey Company from Florida Needs Sweet and Buzz-worthy Site

Website Requests:
-Deluxe 5-Page Website with SSL-Secure Online Store (Shopify)
-High-end imagery to appeal to a discerning consumer
-Detailed verbiage with strong SEO and easy readability
-Design principles: simple, chic, luxe, earthy
Pages:
1. Home {Local, Raw American Honey from Florida}
2. The Hive
> About Us
>Meet the Beekeepers
3. Buy Honey
> Shopify retail store
4. The Buzz {News, Recipes & More}
> Blog
5. Contact Us {We're Buzzin' to Meet You}
> Store Hours
> Phone Number
> Address
> Quick Contact Form
Attachments: Web design notes, Logo, Color Codes, Inspiration Photos
Target Market(s)
High-end honey consumer in the U.S.
Industry/Entity Type
Upscale honey enthusiasts; direct to consumer sales.
Coding
Coded - Design and coding required
Number of Pages Required
5+ page
Requirements
Must have
- Upscale look and feel, easy usability for quick sales.

```html
<!DOCTYPE html>
<html lang="en">
<head>
<meta charset="UTF-8">
<title>Golden Comb — Raw Florida Honey</title>
<link href="https://fonts.googleapis.com/css2?family=Bitter:wght@400;600;700&family=Open+Sans:wght@400;600;700&display=swap" rel="stylesheet">
<style>
:root{
  --ink:#1b191a;
  --ink-2:#232021;
  --gold:#f1c535;
  --gold-soft:#f3ca4f;
  --cream:#f4efe4;
  --muted:#b9b3a8;
  --white:#ffffff;
}
*{box-sizing:border-box;margin:0;padding:0}
html,body{width:1200px;height:3484px;overflow:hidden;background:var(--ink);font-family:"Open Sans",sans-serif;color:var(--white)}
.page{position:relative;width:1200px;height:3484px}

/* header + hero */
.hero{position:absolute;left:0;top:0;width:1200px;height:760px;background:linear-gradient(180deg,#141213 0%,#2a2622 45%,#1a1817 100%)}
.hero-photo{position:absolute;left:0;top:150px;width:1200px;height:610px;background:radial-gradient(ellipse at 60% 55%,#4a3f2b 0%,#2b2520 45%,#171515 100%)}
.brand{position:absolute;left:540px;top:10px;width:120px;text-align:center}
.brand-dot{display:block;width:44px;height:44px;border-radius:50%;background:var(--gold);margin:0 auto 6px}
.brand-name{font-family:"Bitter",serif;font-weight:700;font-size:15px;color:var(--gold);letter-spacing:1px}
.utility{position:absolute;right:120px;top:10px;display:flex;gap:14px;align-items:center}
.search{width:140px;height:22px;border-bottom:1px solid #777;font-size:11px;color:#aaa;display:flex;justify-content:space-between;align-items:center}
.nav{position:absolute;top:112px;left:0;width:1200px;display:flex;justify-content:center;gap:46px}
.nav a{font-family:"Bitter",serif;font-weight:700;font-size:19px;color:var(--gold);text-decoration:none;text-transform:uppercase;letter-spacing:.5px}
.hero-title{position:absolute;top:330px;left:0;width:1200px;text-align:center;font-family:"Bitter",serif;font-weight:700;font-size:46px;line-height:1.3;color:var(--white)}
.btn{display:inline-block;border:1.5px solid var(--white);color:var(--white);font-size:17px;padding:14px 26px;text-decoration:none}
.hero .btn{position:absolute;top:510px;left:516px}

/* about */
.about{position:absolute;top:760px;left:0;width:1200px;height:660px;background:var(--ink)}
.rule{display:block;width:50px;height:3px;background:var(--gold)}
.about .rule{margin:90px auto 18px}
.about h2{text-align:center;font-family:"Bitter",serif;font-weight:400;font-size:34px;color:var(--gold)}
.about p{width:800px;margin:26px auto 0;text-align:center;font-size:13px;line-height:1.75;color:var(--cream)}
.features{position:absolute;top:390px;left:120px;width:960px;display:flex;justify-content:space-between}
.feature{width:160px;text-align:center}
.feature svg{display:block;margin:0 auto}
.feature span{display:block;margin-top:14px;font-family:"Bitter",serif;font-weight:700;font-size:17px;color:var(--gold)}

/* gallery */
.photo{position:absolute}
.p1{left:0;top:1420px;width:400px;height:370px;background:linear-gradient(135deg,#e7d2a8,#c8872a)}
.p2{left:400px;top:1420px;width:400px;height:370px;background:linear-gradient(135deg,#f6e28a,#e7a21a)}
.p3{left:800px;top:1420px;width:400px;height:370px;background:linear-gradient(135deg,#6b3f1d,#d79a2e)}
.p4{left:0;top:1790px;width:600px;height:450px;background:linear-gradient(160deg,#5a5651,#c9c3b6)}
.p5{left:0;top:2260px;width:600px;height:360px;background:linear-gradient(135deg,#7a5132,#c57a1e)}
.p6{left:600px;top:2260px;width:600px;height:360px;background:linear-gradient(135deg,#c58e2a,#efe7d6)}
.p7{left:600px;top:2620px;width:600px;height:460px;background:linear-gradient(135deg,#1d1c1c,#3a342c)}
.story{position:absolute;background:var(--ink-2);padding-left:90px}
.story h3{font-family:"Bitter",serif;font-weight:400;font-size:28px;line-height:1.3;color:var(--gold);margin-top:18px;width:420px}
.story p{font-size:13px;line-height:1.6;color:var(--cream);margin:18px 0 26px;width:380px}
.s1{left:600px;top:1790px;width:600px;height:450px;padding-top:158px}
.s2{left:0;top:2620px;width:600px;height:460px;padding-top:152px;background:var(--ink)}

/* footer */
.footer{position:absolute;top:3080px;left:0;width:1200px;height:404px;background:var(--gold-soft);color:var(--ink)}
.social{position:absolute;left:100px;top:98px;display:flex;gap:20px}
.social i{display:block;width:22px;height:22px;border-radius:50%;background:var(--ink)}
.contact{position:absolute;left:100px;top:150px}
.contact h4{font-size:17px;font-weight:600;margin-bottom:4px}
.contact p{font-size:13px;line-height:1.5;margin-bottom:18px}
.links{position:absolute;left:500px;top:98px;list-style:none}
.links li{font-size:13px;margin-bottom:42px}
.signup{position:absolute;left:750px;top:98px;width:410px}
.signup h4{font-size:17px;font-weight:600;margin-bottom:26px}
.signup form{display:flex}
.signup .field{flex:1;height:40px;background:var(--white);font-size:12px;padding:12px;color:#777}
.signup .send{width:130px;height:40px;background:var(--ink);color:var(--white);font-size:12px;display:flex;align-items:center;justify-content:center}
.signup p{font-size:13px;line-height:1.55;margin-top:22px;width:330px}
.copy{position:absolute;left:100px;top:350px;font-size:12px}
.top{position:absolute;right:40px;top:350px;font-size:12px}
</style>
</head>
<body>
<div class="page">

  <header class="hero">
    <div class="hero-photo" role="img" aria-label="Dark photo of boxed honey gift sets with jars"></div>
    <div class="brand"><span class="brand-dot"></span><span class="brand-name">GOLDEN COMB</span></div>
    <div class="utility">
      <svg width="20" height="18" viewBox="0 0 20 18"><path d="M1 2h3l2 10h10l2-7H5" fill="none" stroke="#bbb" stroke-width="1.5"/><circle cx="8" cy="15.5" r="1.5" fill="#bbb"/><circle cx="15" cy="15.5" r="1.5" fill="#bbb"/></svg>
      <div class="search"><span>Search</span><svg width="12" height="12" viewBox="0 0 12 12"><circle cx="5" cy="5" r="4" fill="none" stroke="#bbb" stroke-width="1.4"/><path d="M8 8l3.5 3.5" stroke="#bbb" stroke-width="1.4"/></svg></div>
    </div>
    <nav class="nav">
      <a href="#">Home</a><a href="#">The Hive</a><a href="#">Buy Honey</a><a href="#">The Buzz</a><a href="#">Contact Us</a>
    </nav>
    <h1 class="hero-title">Blessed to Bee-keep Straight<br>from our beloved hives to your<br>lovely home</h1>
    <a class="btn" href="#">Watch Video</a>
  </header>

  <section class="about">
    <span class="rule"></span>
    <h2>About Us</h2>
    <p>Every jar we sell is raw, unfiltered Florida honey gathered from our own family hives in the heart of Lake County. We are a small agricultural farm devoted to pure American honey and to the health of the pollinators who make it. Our honey travels straight from the hive to your table with no heating, blending or added sugar. Orange blossom, gallberry, wildflower and seasonal varieties are bottled by hand, and our bees forage across more than a thousand acres of native bloom.</p>
    <div class="features">
      <div class="feature">
        <svg width="100" height="110" viewBox="0 0 100 110"><polygon points="50,4 94,29 94,81 50,106 6,81 6,29" fill="none" stroke="#f1c535" stroke-width="3"/><text x="50" y="52" text-anchor="middle" font-family="Bitter,serif" font-weight="700" font-size="18" fill="#f1c535">100%</text><text x="50" y="74" text-anchor="middle" font-family="Bitter,serif" font-weight="700" font-size="18" fill="#f1c535">RAW</text></svg>
        <span>Unfiltered Honey</span>
      </div>
      <div class="feature">
        <svg width="100" height="110" viewBox="0 0 100 110"><polygon points="50,4 94,29 94,81 50,106 6,81 6,29" fill="none" stroke="#f1c535" stroke-width="3"/><polygon points="50,32 70,44 70,66 50,78 30,66 30,44" fill="none" stroke="#f1c535" stroke-width="3"/></svg>
        <span>Pure Honey</span>
      </div>
      <div class="feature">
        <svg width="100" height="110" viewBox="0 0 100 110"><polygon points="50,4 94,29 94,81 50,106 6,81 6,29" fill="none" stroke="#f1c535" stroke-width="3"/><path d="M32 74C32 48 50 34 70 34C70 60 54 74 32 74Z M32 74L62 44" fill="none" stroke="#f1c535" stroke-width="3"/></svg>
        <span>Special Crops</span>
      </div>
      <div class="feature">
        <svg width="100" height="110" viewBox="0 0 100 110"><polygon points="50,4 94,29 94,81 50,106 6,81 6,29" fill="none" stroke="#f1c535" stroke-width="3"/><path d="M50 30V82 M50 46L38 38 M50 46L62 38 M50 58L38 50 M50 58L62 50 M50 70L38 62 M50 70L62 62" fill="none" stroke="#f1c535" stroke-width="3"/></svg>
        <span>Natural Honey</span>
      </div>
      <div class="feature">
        <svg width="100" height="110" viewBox="0 0 100 110"><polygon points="50,4 94,29 94,81 50,106 6,81 6,29" fill="none" stroke="#f1c535" stroke-width="3"/><rect x="36" y="40" width="28" height="38" rx="4" fill="none" stroke="#f1c535" stroke-width="3"/><rect x="40" y="32" width="20" height="8" fill="none" stroke="#f1c535" stroke-width="3"/></svg>
        <span>More Flavours</span>
      </div>
    </div>
  </section>

  <div class="photo p1" role="img" aria-label="Photo of honey tea with lemon and a honey dipper"></div>
  <div class="photo p2" role="img" aria-label="Photo of golden honeycomb pieces"></div>
  <div class="photo p3" role="img" aria-label="Photo of honey jars and dipper on a wooden table"></div>

  <div class="photo p4" role="img" aria-label="Photo of a honey jar beside its gift box"></div>
  <section class="story s1">
    <span class="rule"></span>
    <h3>Don’t Judge a Bee by Its Stinger</h3>
    <p>If the bee disappeared off the face of the Earth, man would have only four years left to live.</p>
    <a class="btn" href="#">View All</a>
  </section>

  <div class="photo p5" role="img" aria-label="Photo of honey jars wrapped in burlap with mint leaves"></div>
  <div class="photo p6" role="img" aria-label="Photo of three honey bottles in a gift box"></div>

  <section class="story s2">
    <span class="rule"></span>
    <h3>Real Local Honey, Really Good for You</h3>
    <p>Raw honey is loaded with antioxidants to protect your body from cell damage due to free radicals.</p>
    <a class="btn" href="#">Read More</a>
  </section>
  <div class="photo p7" role="img" aria-label="Photo of dark gift boxes holding honey jars"></div>

  <footer class="footer">
    <div class="social"><i></i><i></i></div>
    <div class="contact">
      <h4>Address</h4>
      <p>1480 Orchard Lane,<br>Mount Dora, FL 32757</p>
      <h4>Phone Number</h4>
      <p>(352) 555-0148</p>
    </div>
    <ul class="links">
      <li>Home</li><li>The Hive</li><li>Buy Honey</li><li>The Buzz</li><li>Contact us</li>
    </ul>
    <div class="signup">
      <h4>Sign up for Our Emails</h4>
      <form><div class="field">Your Email</div><div class="send">SUBSCRIBE</div></form>
      <p>Our Honey comes straight from our beehives to your table. No filtering, heating, or any funny stuff. Just All Natural, 100% Pure Florida Honey.</p>
    </div>
    <div class="copy">Copyright © 2021, Golden Comb.</div>
    <div class="top">TOP</div>
  </footer>

</div>
</body>
</html>
```